Climbing Gear Company Stationary Design

We need some new stationary to standardise our business.
We require:

Business Card
A4 Letterhead
With complements slip

Our business is a Distributor and retailer of rock climbing equipment throughout Australia.
We need to the stationary (business card in particular) to reflect this.

Target Market(s)

customers, other retail outlets, overseas manufacturers.

Industry/Entity Type

Business

Requirements
Must have
• company logo
website url- www.ridgetopgearworks.com.au
email - mark@ridgetopgearworks.com
Business Address: Unit 3, 14-16 Marlowe Street, Tallowood Bay, NSW, 2371
Phone: 0438 627 194
my Name (on Business card) - Gordon Pellimore
use of Blue colour in our logo

```html
<!DOCTYPE html>
<html lang="en">
<head>
<meta charset="utf-8">
<title>Ridgetop Gearworks Stationery</title>
<link rel="stylesheet" href="https://fonts.googleapis.com/css2?family=Open+Sans:wght@400;600;800&family=Allura&display=swap">
<style>
  :root {
    --bg: #ececec;
    --paper: #ffffff;
    --brand: #1f4fa3;
    --brand-light: #3d8fd6;
    --brand-pale: #7fb7e6;
    --ink: #4a4a4a;
    --ink-soft: #7a7a7a;
  }
  * { margin: 0; padding: 0; box-sizing: border-box; }
  html, body { width: 1200px; height: 795px; overflow: hidden; }
  body {
    background: var(--bg);
    font-family: "Open Sans", Arial, sans-serif;
    color: var(--ink);
    position: relative;
  }

  /* Shared brand lockup */
  .brand-name {
    font-family: "Open Sans", Arial, sans-serif;
    font-weight: 800;
    color: var(--brand);
    text-transform: uppercase;
    letter-spacing: 0.02em;
    line-height: 1;
    display: flex;
    align-items: center;
    gap: 6px;
    white-space: nowrap;
  }
  .brand-dot {
    width: 8px; height: 8px;
    background: var(--brand-light);
    border-radius: 50%;
    flex: none;
  }
  .brand-tagline {
    color: var(--brand-light);
    text-transform: uppercase;
    letter-spacing: 0.18em;
    font-weight: 400;
    margin-top: 4px;
    white-space: nowrap;
  }
  .ridge-band {
    position: absolute;
    left: 0; right: 0;
    background: linear-gradient(180deg, var(--brand-pale) 0%, var(--brand-light) 35%, var(--brand) 100%);
  }

  /* Letterhead */
  .letterhead {
    position: absolute;
    left: 70px; top: 28px;
    width: 522px; height: 738px;
    background: var(--paper);
    box-shadow: 0 4px 14px rgba(0,0,0,0.14);
    overflow: hidden;
  }
  .letterhead .brand {
    position: absolute;
    left: 40px; top: 46px;
  }
  .letterhead .brand-name { font-size: 16px; }
  .letterhead .brand-tagline { font-size: 6px; }
  .letterhead .contact {
    position: absolute;
    left: 290px; top: 44px;
    font-size: 6.5px;
    line-height: 1.6;
    color: var(--ink-soft);
    white-space: nowrap;
  }
  .contact-row { display: flex; align-items: center; gap: 4px; }
  .contact-icon { width: 7px; height: 7px; flex: none; }
  .letterhead .address {
    position: absolute;
    left: 410px; top: 44px;
    font-size: 6.5px;
    line-height: 1.6;
    color: var(--ink-soft);
    white-space: nowrap;
  }
  .letter-body {
    position: absolute;
    left: 68px; top: 150px;
    width: 390px;
    font-size: 8px;
    line-height: 1.55;
    color: var(--ink-soft);
  }
  .letter-body .salutation {
    font-weight: 600;
    color: var(--ink);
    margin-bottom: 10px;
  }
  .letter-body p { margin-bottom: 10px; }
  .signature {
    position: absolute;
    left: 68px; top: 470px;
  }
  .signature-script {
    font-family: "Allura", cursive;
    font-size: 30px;
    color: var(--ink);
    line-height: 1;
  }
  .signature-role {
    font-size: 8px;
    font-weight: 600;
    color: var(--ink);
  }
  .letterhead .ridge-band { bottom: 0; height: 150px; }

  /* Business cards */
  .card {
    position: absolute;
    width: 330px; height: 189px;
    background: var(--paper);
    box-shadow: 0 4px 12px rgba(0,0,0,0.14);
    overflow: hidden;
  }
  .card-back { left: 720px; top: 150px; }
  .card-front { left: 720px; top: 430px; }

  .card-back .ridge-band { top: 0; height: 44px; }
  .card-back .brand {
    position: absolute;
    right: 22px; top: 56px;
    text-align: right;
  }
  .card-back .brand-name { font-size: 14px; justify-content: flex-end; }
  .card-back .brand-tagline { font-size: 5px; }
  .card-holder {
    position: absolute;
    left: 0; right: 0; top: 100px;
    text-align: center;
    font-size: 15px;
    color: var(--ink);
  }
  .card-back .contact {
    position: absolute;
    left: 22px; bottom: 16px;
    font-size: 7px;
    line-height: 1.6;
    color: var(--ink-soft);
    white-space: nowrap;
  }
  .card-back .address {
    position: absolute;
    right: 22px; bottom: 16px;
    font-size: 7px;
    line-height: 1.6;
    color: var(--ink-soft);
    text-align: right;
    white-space: nowrap;
  }

  .card-front .band-top { top: 0; height: 62px; }
  .card-front .band-bottom { bottom: 0; height: 50px; transform: scaleY(-1); }
  .card-front .brand {
    position: absolute;
    left: 0; right: 0; top: 74px;
    display: flex; flex-direction: column; align-items: center;
  }
  .card-front .brand-name { font-size: 19px; }
  .card-front .brand-tagline { font-size: 6.5px; }
  .card-front .web {
    position: absolute;
    left: 0; right: 0; bottom: 58px;
    text-align: center;
    font-size: 7.5px;
    color: var(--brand);
  }
</style>
</head>
<body>

<main class="stationery">

  <section class="letterhead" aria-label="A4 letterhead">
    <div class="brand">
      <div class="brand-name"><span class="brand-dot"></span>Ridgetop Gearworks</div>
      <div class="brand-tagline">Ropes • Racks • Routes</div>
    </div>

    <div class="contact">
      <div class="contact-row">
        <svg class="contact-icon" viewBox="0 0 10 10"><path d="M2 1h2l1 2-1.2 1a5 5 0 0 0 2.2 2.2L7 5l2 1v2a1 1 0 0 1-1 1A7 7 0 0 1 1 2a1 1 0 0 1 1-1z" fill="#1f4fa3"/></svg>
        <span>0438 627 194</span>
      </div>
      <div class="contact-row">
        <svg class="contact-icon" viewBox="0 0 10 10"><rect x="1" y="2.5" width="8" height="5.5" fill="#1f4fa3"/><path d="M1 2.5l4 3 4-3" stroke="#fff" stroke-width="0.8" fill="none"/></svg>
        <span>mark@ridgetopgearworks.com</span>
      </div>
      <div class="contact-row">
        <svg class="contact-icon" viewBox="0 0 10 10"><circle cx="5" cy="5" r="4" fill="#1f4fa3"/></svg>
        <span>www.ridgetopgearworks.com.au</span>
      </div>
    </div>

    <div class="address">
      Unit 3, 14-16 Marlowe Street<br>
      Tallowood Bay NSW 2371
    </div>

    <div class="letter-body">
      <p class="salutation">Lorem Ipsum,</p>
      <p>Cras mattis consectetur purus sit amet fermentum. Etiam porta sem malesuada magna mollis euismod. Integer posuere erat a ante venenatis dapibus posuere velit aliquet. Cras justo odio, dapibus ac facilisis in, egestas eget quam.</p>
      <p>Vivamus sagittis lacus vel augue laoreet rutrum faucibus dolor auctor. Donec sed odio dui. Nullam id dolor id nibh ultricies vehicula ut id elit.</p>
      <p>Donec id elit non mi porta gravida at eget metus. Fusce dapibus, tellus ac cursus commodo, tortor mauris condimentum nibh, ut fermentum massa justo sit amet risus.</p>
      <p>Cum sociis natoque penatibus et magnis dis parturient montes, nascetur ridiculus mus. Morbi leo risus, porta ac consectetur ac, vestibulum at eros.</p>
      <p>Cras justo odio, dapibus ac facilisis in, egestas eget quam. Integer posuere erat a ante venenatis dapibus posuere velit aliquet.</p>
    </div>

    <div class="signature">
      <div class="signature-script">Your Name</div>
      <div class="signature-role">Company Director</div>
    </div>

    <div class="ridge-band" role="img" aria-label="Blue mountain ridge band with torn paper edge"></div>
  </section>

  <section class="card card-back" aria-label="Business card, contact side">
    <div class="ridge-band" role="img" aria-label="Blue mountain ridge band with torn paper edge"></div>
    <div class="brand">
      <div class="brand-name"><span class="brand-dot"></span>Ridgetop Gearworks</div>
      <div class="brand-tagline">Ropes • Racks • Routes</div>
    </div>
    <div class="card-holder">Gordon Pellimore</div>
    <div class="contact">
      <div class="contact-row">
        <svg class="contact-icon" viewBox="0 0 10 10"><path d="M2 1h2l1 2-1.2 1a5 5 0 0 0 2.2 2.2L7 5l2 1v2a1 1 0 0 1-1 1A7 7 0 0 1 1 2a1 1 0 0 1 1-1z" fill="#1f4fa3"/></svg>
        <span>0438 627 194</span>
      </div>
      <div class="contact-row">
        <svg class="contact-icon" viewBox="0 0 10 10"><rect x="1" y="2.5" width="8" height="5.5" fill="#1f4fa3"/><path d="M1 2.5l4 3 4-3" stroke="#fff" stroke-width="0.8" fill="none"/></svg>
        <span>mark@ridgetopgearworks.com</span>
      </div>
    </div>
    <div class="address">
      Unit 3, 14-16 Marlowe Street<br>
      Tallowood Bay NSW 2371
    </div>
  </section>

  <section class="card card-front" aria-label="Business card, brand side">
    <div class="ridge-band band-top" role="img" aria-label="Blue mountain ridge band with torn paper edge"></div>
    <div class="brand">
      <div class="brand-name"><span class="brand-dot"></span>Ridgetop Gearworks</div>
      <div class="brand-tagline">Ropes • Racks • Routes</div>
    </div>
    <div class="web">www.ridgetopgearworks.com.au</div>
    <div class="ridge-band band-bottom" role="img" aria-label="Blue mountain ridge band with torn paper edge"></div>
  </section>

</main>

</body>
</html>
```